Accounting firm needing business card / letterhead designed
Marcus L. Trenholm, CPA
marcus@veltrowledger.com
www.veltrowledger.com
842 E Alder Ave Corvane, MN 43827
419-562-0974

```html
<!DOCTYPE html>
<html lang="en">
<head>
<meta charset="utf-8">
<title>Veltro Ledger – Business Card</title>
<link rel="stylesheet" href="https://fonts.googleapis.com/css2?family=Roboto:wght@400;500&family=Roboto+Condensed:wght@700&display=swap">
<style>
  :root {
    --navy: #241f5c;
    --paper: #f7f7f6;
    --backdrop: #e4e4e4;
    --ink-gray: #4a4a4a;
    --rule: #9a9a9a;
    --white: #ffffff;
  }
  * { margin: 0; padding: 0; box-sizing: border-box; }
  html, body {
    width: 1200px; height: 960px; overflow: hidden;
    background: var(--backdrop);
    font-family: "Roboto", Arial, sans-serif;
  }
  .stage { position: relative; width: 1200px; height: 960px; }
  .card { position: absolute; box-shadow: 1px 2px 4px rgba(0,0,0,0.25); }
  .card-front { left: 314px; top: 113px; width: 602px; height: 343px; background: var(--paper); }
  .card-back  { left: 311px; top: 472px; width: 600px; height: 343px; background: var(--navy); }

  .brand-name {
    position: absolute; right: 36px; top: 44px;
    font-family: "Roboto", Arial, sans-serif; font-weight: 500;
    font-size: 38px; letter-spacing: 1px; color: var(--navy); white-space: nowrap;
  }
  .holder-name {
    position: absolute; left: 34px; top: 208px;
    font-family: "Roboto Condensed", "Arial Narrow", sans-serif; font-weight: 700;
    font-size: 21px; color: var(--navy);
  }
  .divider { position: absolute; left: 34px; right: 37px; top: 242px; height: 1px; background: var(--rule); }
  .contact-list { position: absolute; left: 34px; top: 255px; list-style: none; }
  .contact-list li {
    display: flex; align-items: center; gap: 8px;
    height: 19px; font-size: 14.5px; color: var(--ink-gray);
  }
  .contact-list svg { width: 14px; height: 14px; fill: var(--navy); flex: none; }
  .address {
    position: absolute; right: 36px; top: 275px; text-align: right;
    font-size: 14.5px; line-height: 19px; color: var(--ink-gray); font-style: normal;
  }

  .brand-name-reverse {
    position: absolute; right: 38px; top: 232px;
    font-weight: 500; font-size: 34px; letter-spacing: 1px; color: var(--white); white-space: nowrap;
  }
  .back-url {
    position: absolute; right: 33px; top: 292px;
    font-size: 14px; letter-spacing: 1.6px; color: var(--white);
  }
</style>
</head>
<body>
<main class="stage">
  <section class="card card-front" aria-label="Business card front">
    <div class="brand-name">VELTRO LEDGER</div>
    <h1 class="holder-name">Marcus L. Trenholm, CPA</h1>
    <div class="divider"></div>
    <ul class="contact-list">
      <li>
        <svg viewBox="0 0 16 16" aria-hidden="true"><path d="M3.6 1.2l2.3 2.6-1.3 1.8c.9 2 2.3 3.5 4.3 4.4l1.8-1.3 2.6 2.3-1.1 2.5C6.8 13.5 2.5 9.2 1.1 2.3z"/></svg>
        555-562-0974
      </li>
      <li>
        <svg viewBox="0 0 16 16" aria-hidden="true"><path d="M1 3h14v1.2L8 8.6 1 4.2z"/><path d="M1 5.6l7 4.4 7-4.4V13H1z"/></svg>
        marcus@veltrowledger.com
      </li>
      <li>
        <svg viewBox="0 0 16 16" aria-hidden="true"><circle cx="8" cy="8" r="7"/><path d="M5 4.5c1.5.2 2 1.3 1.3 2.3-.8 1 .5 2 1.4 2.6.6.5.2 1.9-.3 3M10.5 3c-.6 1.2.2 2 1.2 2.3.9.3 1.3 1.5 1 2.7" stroke="#f7f7f6" stroke-width="1.2" fill="none"/></svg>
        www.veltrowledger.com
      </li>
    </ul>
    <address class="address">842 E Alder Ave<br>Corvane, MN 43827</address>
  </section>

  <section class="card card-back" aria-label="Business card back">
    <div class="brand-name-reverse">VELTRO LEDGER</div>
    <div class="back-url">www.veltrowledger.com</div>
  </section>
</main>
</body>
</html>
```